Modern and professional facebook ad for disability service

Design a facebook ad for a disability service. Want something bright and fun and eyecatching. Would ideally like a carousel ad as this will give us more options to provide information.
CONTENT:
- Looking for a Plan Manager who will support your QWTR journey so that you can focus on living your best possible life and achieve your QWTR Goals?
- Then join the Wattlebrook Plan Management family today - quick and easy sign up.
- Friendly, Reliable, Responsive Service
- Dedicate Plan Managers so you always speak to the same person
- Fast Payment of Provider Invoices
- Supporting you to live Your Life, Your Way
- Call us today on 1300 482 316
- www.wattlebrookplanmanagement.com.au
Updates

Sick

Target Market(s)

Disability Sector

Font styles to use
Other font styles liked:
• Raleway

Requirements
Must have
• Bright colours and eye catching design

```html
<!DOCTYPE html>
<html lang="en">
<head>
<meta charset="utf-8">
<title>Dedicate Plan Managers – Wattlebrook Plan Management</title>
<link rel="stylesheet" href="https://fonts.googleapis.com/css2?family=Raleway:ital,wght@0,500;1,500&display=swap">
<style>
  :root {
    --purple-text: #6a2a78;
    --green-bright: #3fc24f;
    --green-photo-light: #46b34a;
    --green-photo-dark: #2c7a32;
    --purple-blob-a: #a422b8;
    --purple-blob-b: #bb48cb;
    --dot-blue: #c8d8ee;
    --white: #ffffff;
  }
  html, body {
    margin: 0;
    padding: 0;
    width: 1200px;
    height: 1200px;
    overflow: hidden;
    background: var(--white);
  }
  .ad-slide {
    position: relative;
    width: 1200px;
    height: 1200px;
    overflow: hidden;
    background: var(--white);
    font-family: "Raleway", sans-serif;
  }
  .shapes {
    position: absolute;
    inset: 0;
  }
  .headline {
    position: absolute;
    left: 608px;
    top: 126px;
    margin: 0;
    font-weight: 500;
    font-size: 82px;
    line-height: 106px;
    color: var(--purple-text);
    letter-spacing: -0.5px;
  }
  .subline {
    position: absolute;
    left: 609px;
    top: 346px;
    margin: 0;
    font-style: italic;
    font-weight: 500;
    font-size: 31px;
    line-height: 47px;
    color: var(--green-bright);
  }
  .person-photo {
    position: absolute;
    left: 294px;
    top: 368px;
    width: 322px;
    height: 832px;
    border-radius: 140px 140px 40px 40px;
    background: linear-gradient(180deg, #2b2b2b 0%, #6cc25a 28%, #79cf68 55%, #1d1d1d 70%, #141414 100%);
  }
  .dot-grid {
    position: absolute;
    left: 904px;
    top: 741px;
    width: 158px;
    height: 268px;
    border-radius: 40px;
    background: var(--dot-blue);
    opacity: 0.45;
  }
</style>
</head>
<body>
  <main class="ad-slide">
    <svg class="shapes" width="1200" height="1200" viewBox="0 0 1200 1200" aria-hidden="false">
      <defs>
        <linearGradient id="greenPhotoFill" x1="0" y1="0" x2="1" y2="1">
          <stop offset="0" stop-color="var(--green-photo-dark)"/>
          <stop offset="0.5" stop-color="var(--green-photo-light)"/>
          <stop offset="1" stop-color="var(--green-photo-dark)"/>
        </linearGradient>
        <linearGradient id="purpleBlobFill" x1="0" y1="0" x2="1" y2="0">
          <stop offset="0" stop-color="var(--purple-blob-a)"/>
          <stop offset="1" stop-color="var(--purple-blob-b)"/>
        </linearGradient>
      </defs>

      <path class="photo-blob" role="img" aria-label="Green-tinted photo of a child playing on a carpeted floor with an adult"
            d="M0 0 H459 C425 188 325 512 0 572 Z" fill="url(#greenPhotoFill)"/>

      <path class="purple-blob" role="img" aria-label="Purple blob with soft dot texture"
            d="M0 1200 V1025 C70 960 100 820 150 760 C200 690 250 645 310 640 C420 640 560 680 630 760 C700 850 728 1000 728 1200 Z"
            fill="url(#purpleBlobFill)"/>

      <g class="target-icon" fill="none" stroke="var(--green-bright)">
        <ellipse cx="532" cy="205" rx="38" ry="33" stroke-width="16" transform="rotate(-20 532 205)"/>
        <circle cx="536" cy="200" r="10" fill="var(--green-bright)" stroke="none"/>
        <line x1="540" y1="196" x2="578" y2="158" stroke-width="6" stroke-linecap="round"/>
        <path d="M570 148 L584 152 L588 166 L576 162 Z M580 146 L590 147 L588 156 Z" fill="var(--green-bright)" stroke-width="3" stroke-linejoin="round"/>
      </g>

      <path class="brush-stroke" d="M544 514 C650 490 780 455 887 450 C980 448 1080 480 1147 508"
            fill="none" stroke="var(--green-bright)" stroke-width="11" stroke-linecap="round"/>
    </svg>

    <h1 class="headline">Dedicate<br>Plan Managers</h1>
    <p class="subline">so you always speak to the<br>same person</p>

    <div class="person-photo" role="img" aria-label="Photo of a smiling man in a hat, sunglasses and green jacket leaning on a white cane"></div>
    <div class="dot-grid" role="img" aria-label="Light blue dot grid decoration"></div>
  </main>
</body>
</html>
```